CAMBRAI CELEBRATES ANDOUILETTE

On the occasion of the big annual sale, in CAMBRAI, the 57th celebrates the Cambrai specialty "andouillette de CAMBRAI".

On this occasion, we are developing a special menu for this day;

- Authentic CAMBRAI sausage, old-fashioned mustard sauce, served with fresh fries cooked in beef fat and green salad
- CAMBRAI andouillette salad (lettuce, tomatoes, onions, CAMBRAI andouillette, Tome de CAMBRAI, Cambrai apples
- Andouillette gratin (Homemade mash, CAMBRAI andouillette, old-fashioned mustard, gratin with CAMBRAI tome
- BRUSCHETTA: Cream base, CAMBRAI sausage, CAMBRAI tome, onions, old-fashioned mustard
- Grilled ham
- Fried mussels, with CAMBRAI tome cream

The event will take place on Sunday July 2, in continuous service.

Please write in French, and insert the logo of the establishment of 57 and illustrate well.

THANKS

```html
<!DOCTYPE html>
<html lang="fr">
<head>
<meta charset="utf-8">
<title>Le 57 – Andouillette de Cambrai</title>
<link rel="stylesheet" href="https://fonts.googleapis.com/css2?family=Abril+Fatface&family=Poppins:wght@400;500;600;700;800&family=Yellowtail&display=swap">
<style>
  :root{
    --gold:#a07d40;
    --gold-text:#b58b3e;
    --gold-title:#c9a04a;
    --black:#0c0c0c;
    --white:#ffffff;
    --yellow:#efe479;
    --script:#f3ea6c;
    --rule:#c9b48a;
    --silver:#d9d9d9;
    --ink:#1a1a1a;
    --page:#f2f2f2;
  }
  html,body{margin:0;padding:0;width:1200px;height:3096px;overflow:hidden;background:var(--page);}
  .canvas{position:relative;width:1200px;height:3096px;}
  .poster{
    position:absolute;left:32px;top:743px;width:812px;height:1150px;
    transform:scale(1.4);transform-origin:0 0;
    background:var(--white);overflow:hidden;
    box-shadow:0 4px 14px rgba(0,0,0,.25);
    font-family:'Poppins',sans-serif;
  }
  .poster-frame{position:absolute;left:0;top:0;width:812px;height:1150px;}
  .abs{position:absolute;left:0;width:812px;text-align:center;}
  .logo-disc{
    position:absolute;left:310px;top:-15px;width:180px;height:180px;border-radius:50%;
    background:var(--white);display:flex;align-items:center;justify-content:center;
  }
  .logo-name{font-family:'Abril Fatface',serif;font-size:44px;color:var(--black);line-height:1;}
  .headline{top:160px;font-family:'Abril Fatface',serif;font-size:38px;color:var(--white);line-height:1;}
  .city-pill{
    position:absolute;left:282px;top:220px;width:248px;height:38px;border-radius:12px;
    background:var(--yellow);color:var(--black);font-weight:700;font-size:28px;
    display:flex;align-items:center;justify-content:center;line-height:1;
  }
  .celebrates{top:274px;font-weight:700;font-size:19px;color:var(--white);letter-spacing:-.2px;}
  .celebrates .num{color:var(--gold-title);}
  .celebrates sup{font-size:10px;}
  .specialty{top:300px;font-family:'Abril Fatface',serif;font-size:48px;color:var(--gold-title);line-height:1;}
  .divider{position:absolute;}
  .developing{position:absolute;left:190px;top:393px;font-weight:700;font-size:15px;color:var(--white);}
  .special-menu{position:absolute;left:160px;top:392px;font-family:'Yellowtail',cursive;font-size:100px;color:var(--script);line-height:1;}
  .for-day{position:absolute;left:532px;top:482px;font-weight:700;font-size:15px;color:var(--white);}
  .food{position:absolute;left:0;top:505px;width:812px;height:210px;}
  .menu{position:absolute;left:80px;top:738px;width:652px;margin:0;padding:0;list-style:none;text-align:center;}
  .menu-item{border-bottom:1px solid var(--rule);padding:0 0 4px;margin-bottom:9px;}
  .menu-item:last-child{border-bottom:none;}
  .dish{display:block;color:var(--gold-text);font-weight:600;font-size:16px;line-height:19px;}
  .desc{display:block;color:var(--ink);font-size:11.5px;line-height:15px;white-space:nowrap;}
  .event-label{
    position:absolute;left:218px;top:996px;width:376px;height:26px;box-sizing:border-box;
    border:1.5px solid var(--ink);border-radius:8px;text-align:center;
    font-weight:700;font-size:15.5px;line-height:24px;color:var(--ink);
  }
  .date{position:absolute;left:0;top:1036px;width:812px;display:flex;justify-content:center;align-items:center;gap:6px;color:var(--black);font-weight:800;font-size:24px;}
  .day-badge{width:36px;height:36px;border-radius:50%;background:var(--black);color:var(--white);font-size:15px;display:flex;align-items:center;justify-content:center;}
  .day-badge sup{font-size:8px;}
  .service{margin-left:8px;background:var(--gold);color:var(--white);font-weight:700;font-size:17px;padding:1px 10px;border-radius:6px;}
  .follow{position:absolute;left:0;top:1080px;width:812px;display:flex;justify-content:center;align-items:center;gap:6px;font-size:14px;color:var(--black);}
  .social-dot{width:14px;height:14px;border-radius:50%;background:var(--black);}
</style>
</head>
<body>
<div class="canvas">
  <div class="poster">
    <svg class="poster-frame" viewBox="0 0 812 1150" aria-hidden="true">
      <rect x="0" y="0" width="812" height="292" fill="var(--gold)"/>
      <path d="M0 292 C50 292 70 275 72 240 L74 95 C76 40 100 22 170 18 L330 12 L482 12 L640 18 C712 22 736 40 738 95 L740 240 C742 275 762 292 812 292 L812 330 C770 330 752 350 752 400 L752 470 C752 520 730 540 680 545 L130 545 C82 540 60 520 60 470 L60 400 C60 350 42 330 0 330 Z"
            fill="var(--black)" stroke="var(--silver)" stroke-width="3"/>
      <rect x="0" y="1100" width="812" height="50" fill="var(--gold)"/>
      <path d="M20 1100 L792 1100 L792 1118 L20 1118 Z" fill="var(--white)"/>
      <line x1="22" y1="1120" x2="790" y2="1120" stroke="var(--white)" stroke-width="4" stroke-dasharray="3 3"/>
    </svg>

    <div class="logo-disc"><span class="logo-name">Le 57</span></div>

    <div class="abs headline">Grande vente annuelle</div>
    <div class="city-pill">À CAMBRAI</div>
    <div class="abs celebrates">THE <span class="num">57<sup>TH</sup></span> CELEBRATES THE CAMBRAI SPECIALTY</div>
    <div class="abs specialty">Andouillette de CAMBRAI</div>

    <svg class="divider" style="left:220px;top:359px" width="372" height="16" viewBox="0 0 372 16" aria-hidden="true">
      <line x1="10" y1="8" x2="362" y2="8" stroke="var(--gold-title)" stroke-width="1.5"/>
      <path d="M2 8 L10 2 L18 8 L10 14 Z M354 8 L362 2 L370 8 L362 14 Z" fill="var(--gold-title)"/>
    </svg>

    <div class="developing">WE ARE DEVELOPING A</div>
    <div class="special-menu">Special Menu</div>
    <div class="for-day">FOR THIS DAY</div>

    <svg class="food" viewBox="0 0 812 210" role="img" aria-label="Photo des plats : bruschettas sur planche, andouillettes de Cambrai grillées dans un plat blanc, salade d'andouillette aux tomates">
      <defs>
        <radialGradient id="plateWood" cx="50%" cy="55%" r="55%">
          <stop offset="0" stop-color="#d9a56a"/><stop offset="1" stop-color="#9c6a3a"/>
        </radialGradient>
        <radialGradient id="sausage" cx="50%" cy="45%" r="55%">
          <stop offset="0" stop-color="#e0894f"/><stop offset="1" stop-color="#9b4a24"/>
        </radialGradient>
        <radialGradient id="salad" cx="50%" cy="50%" r="55%">
          <stop offset="0" stop-color="#6f8c4a"/><stop offset="1" stop-color="#dfe3df"/>
        </radialGradient>
      </defs>
      <ellipse cx="120" cy="95" rx="125" ry="85" fill="url(#plateWood)" opacity=".9"/>
      <ellipse cx="405" cy="130" rx="160" ry="78" fill="url(#plateWood)"/>
      <ellipse cx="405" cy="85" rx="125" ry="65" fill="url(#sausage)"/>
      <ellipse cx="690" cy="95" rx="130" ry="80" fill="url(#salad)"/>
    </svg>

    <ul class="menu">
      <li class="menu-item"><span class="dish">Authentique saucisse de CAMBRAI,</span><span class="desc">sauce moutarde à l'ancienne, servie avec frites fraîches cuites au gras de bœuf et salade verte</span></li>
      <li class="menu-item"><span class="dish">Salade d'andouillette CAMBRAI</span><span class="desc">(salade, tomates, oignons, andouillette CAMBRAI, Tome de CAMBRAI, pommes Cambrai</span></li>
      <li class="menu-item"><span class="dish">Gratin d'andouillettes</span><span class="desc">(Purée maison, andouillette CAMBRAI, moutarde à l'ancienne, gratinée à la tome CAMBRAI</span></li>
      <li class="menu-item"><span class="dish">BRUSCHETTA:</span><span class="desc">Base crème, saucisse CAMBRAI, tome CAMBRAI, oignons, moutarde à l'ancienne Jambon grillé</span></li>
      <li class="menu-item"><span class="dish">Moules frites,</span><span class="desc">à la crème de Tome CAMBRAI</span></li>
    </ul>

    <svg class="divider" style="left:200px;top:967px" width="412" height="16" viewBox="0 0 412 16" aria-hidden="true">
      <line x1="10" y1="8" x2="402" y2="8" stroke="var(--ink)" stroke-width="1.5"/>
      <path d="M2 8 L10 2 L18 8 L10 14 Z M394 8 L402 2 L410 8 L402 14 Z" fill="var(--ink)"/>
    </svg>

    <div class="event-label">L'ÉVÉNEMENT AURA LIEU LE</div>
    <div class="date">
      <span>SUNDAY</span>
      <span class="day-badge">2<sup>ND</sup></span>
      <span>JULY</span>
      <span class="service">en service continu</span>
    </div>
    <div class="follow"><span>follow us on Chatterly</span><span class="social-dot"></span></div>
  </div>
</div>
</body>
</html>
```